Building company buisness cards

We are looking for a sharp modern new look for our business cards.
We are a New Zealand based company that specialises in house and land packages.
We have attached a photo of the current logo and would like to see if it can be improved somehow if needed.
We are open to any colours but we have chosen green at this stage.
Feel free to change the font and make the logo smarter looking.
Play with the colours and see what looks best.

We want a card that looks so good know one will want to throw it away!

Target Market(s)

Home buyers

Industry/Entity Type

Building

Contact Information for Business Card

Derek Tolvane
0217394062
dtolvane@quillmarkhomesteads.co.nz
quillmarkhomesteads.co.nz

Font styles to use
Serif
Sans Serif

Colors

Designer to choose colors to be used in the design.

Requirements
Must have
• Logo and company name on one side, details on the other side
Nice to have
• Color codes for the original green are HEX #4a8028, RGB(74,128,40), CMYK(42,0,69,50)
• Round corners, Raised and/or spot UV

```html
<!DOCTYPE html>
<html lang="en">
<head>
<meta charset="utf-8">
<title>Quillmark Homesteads – Business Cards</title>
<link rel="stylesheet" href="https://fonts.googleapis.com/css2?family=Lato:wght@400;700&family=Roboto:wght@700&display=swap">
<style>
  :root {
    --brand-green: #4a8028;
    --tab-shadow: #151515;
    --paper: #ffffff;
    --ink: #222222;
    --backdrop: #1d1d1d;
  }
  * { box-sizing: border-box; margin: 0; padding: 0; }
  html, body { width: 1200px; height: 960px; overflow: hidden; }
  body {
    background: var(--backdrop);
    position: relative;
    font-family: "Lato", sans-serif;
  }
  .card {
    position: absolute;
    left: 250px;
    width: 700px;
    height: 400px;
    border-radius: 10px;
    overflow: hidden;
  }

  /* Back side */
  .card-back { top: 60px; background: var(--brand-green); }
  .card-back .brand-name {
    position: absolute;
    left: 0; right: 0; top: 140px;
    text-align: center;
    font-family: "Lato", sans-serif;
    font-weight: 700;
    font-size: 44px;
    line-height: 1;
    color: var(--paper);
  }
  .card-back .website {
    position: absolute;
    left: 60px; bottom: 60px;
    font-size: 17px;
    letter-spacing: 2.4px;
    color: var(--paper);
  }

  /* Front side */
  .card-front { top: 500px; background: var(--paper); }
  .name-tab {
    position: absolute;
    left: 0; top: 38px;
    width: 330px; height: 100px;
  }
  .name-tab svg { position: absolute; inset: 0; }
  .name-tab .person {
    position: absolute;
    left: 70px; top: 14px;
    color: var(--paper);
    font-family: "Roboto", sans-serif;
    font-weight: 700;
  }
  .person .full-name { font-size: 28px; line-height: 1.1; }
  .person .job-title { font-size: 21px; line-height: 1.1; }

  .contact-list {
    position: absolute;
    left: 0; top: 190px;
    list-style: none;
  }
  .contact-item {
    display: flex;
    align-items: center;
    height: 42px;
    margin-bottom: 6px;
  }
  .contact-item .lead-line {
    width: 58px; height: 5px;
    background: var(--brand-green);
  }
  .contact-item .icon {
    width: 30px; height: 30px;
    border: 2px solid var(--brand-green);
    border-radius: 50%;
    display: flex; align-items: center; justify-content: center;
    margin-right: 16px;
  }
  .contact-item .icon svg { width: 16px; height: 16px; fill: var(--brand-green); }
  .contact-item .detail { font-size: 21px; color: var(--ink); }

  .company-name {
    position: absolute;
    right: 60px; top: 150px;
    width: 240px;
    text-align: center;
    font-family: "Lato", sans-serif;
    font-weight: 700;
    font-size: 28px;
    line-height: 1.15;
    color: var(--brand-green);
  }
</style>
</head>
<body>

  <section class="card card-back" aria-label="Card back">
    <p class="brand-name">Quillmark Homesteads</p>
    <p class="website">www.quillmarkhomesteads.co.nz</p>
  </section>

  <section class="card card-front" aria-label="Card front">
    <div class="name-tab">
      <svg viewBox="0 0 330 100" width="330" height="100" aria-hidden="true">
        <polygon points="0,8 330,8 312,100 0,100" fill="var(--tab-shadow)"/>
        <polygon points="0,0 320,0 320,78 0,78" fill="var(--brand-green)"/>
      </svg>
      <div class="person">
        <p class="full-name">Derek Tolvane</p>
        <p class="job-title">Title</p>
      </div>
    </div>

    <ul class="contact-list">
      <li class="contact-item">
        <span class="lead-line"></span>
        <span class="icon"><svg viewBox="0 0 16 16"><path d="M3.5 1.5l2.5 0 1 3.5-1.8 1.2a9 9 0 0 0 4.6 4.6L11 9l3.5 1v2.5c0 1-1 2-2 2C6.5 14.5 1.5 9.5 1.5 3.5c0-1 1-2 2-2z"/></svg></span>
        <span class="detail">0217394062</span>
      </li>
      <li class="contact-item">
        <span class="lead-line"></span>
        <span class="icon"><svg viewBox="0 0 16 16"><path d="M1 3.5h14v9H1zM2.2 4.5L8 9l5.8-4.5v.9L8 10 2.2 5.4z"/></svg></span>
        <span class="detail">dtolvane@quillmarkhomesteads.co.nz</span>
      </li>
      <li class="contact-item">
        <span class="lead-line"></span>
        <span class="icon"><svg viewBox="0 0 16 16"><path d="M8 1a7 7 0 1 0 0 14A7 7 0 0 0 8 1zm0 1.3c.9 1 1.5 2.4 1.7 4H6.3C6.5 4.7 7.1 3.3 8 2.3zM2.4 7.3h2.6c0 1.5.4 2.9 1 4a5.7 5.7 0 0 1-3.6-4zm0-1.3A5.7 5.7 0 0 1 6 2.3c-.6 1.1-1 2.5-1 3.7zm3.9 1.3h3.4c-.1 1.6-.8 3-1.700 4.2-.9-1.2-1.6-2.6-1.7-4.2zm4.7 0h2.6a5.7 5.7 0 0 1-3.6 4c.6-1.1 1-2.5 1-4zm0-1.3c0-1.2-.4-2.6-1-3.7a5.7 5.7 0 0 1 3.6 3.7z"/></svg></span>
        <span class="detail">www.quillmarkhomesteads.co.nz</span>
      </li>
    </ul>

    <p class="company-name">Quillmark<br>Homesteads</p>
  </section>

</body>
</html>
```